first fantastic look and impression

We are looking for a concept for letterhead, business card, emailfooter and template for invoices or offers for our company in the consultation business.
The dancer is a symbol who we are: it looks simple, but there is a lot of hard work and many years of training in this movement. The look is also what we want: elegant, modern, strong, with a touch of extravaganza
Target Market(s)
Hotelbusiness , Consulting
Font styles to use
Sans Serif
Other font styles liked:
- please give us a option we are open
Requirements
Must have
- We are not typical consultants but sparring partners and coaches for the hotel and that should also be expressed in the design. Maybe there is an icon that supports the whole thing. We are more modern and bolder than our industry colleagues.
we are modern, fresh, agile, fast
Nice to have
- a icon

```html
<!DOCTYPE html>
<html lang="en">
<head>
<meta charset="utf-8">
<title>Veltmoor – Business Card</title>
<link href="https://fonts.googleapis.com/css2?family=Montserrat:wght@500;700&family=Roboto:wght@400;500&display=swap" rel="stylesheet">
<style>
  :root {
    --backdrop: #8d8d8d;
    --paper: #ffffff;
    --ink: #121420;
    --navy: #181b27;
    --navy-soft: #20242f;
    --on-dark: #ffffff;
  }
  * { margin: 0; padding: 0; box-sizing: border-box; }
  html, body {
    width: 1188px; height: 1200px; overflow: hidden;
    background: var(--backdrop);
  }
  .sheet { position: relative; width: 1188px; height: 1200px; }

  .card {
    position: absolute; left: 245px; width: 696px; height: 386px; overflow: hidden;
  }
  .card--front { top: 159px; display: flex; }
  .card--back { top: 627px; background: var(--navy); }

  .front-brand {
    width: 355px; height: 100%; background: var(--paper);
    display: flex; align-items: center; justify-content: center;
  }
  .brand-name {
    font-family: "Montserrat", sans-serif; font-weight: 500;
    letter-spacing: 0.06em; color: var(--ink);
  }
  .front-brand .brand-name { font-size: 38px; }

  .front-details {
    flex: 1; height: 100%; background: var(--ink); color: var(--on-dark);
    padding: 98px 0 0 34px;
    font-family: "Roboto", sans-serif;
  }
  .person-name {
    font-family: "Montserrat", sans-serif; font-weight: 700;
    font-size: 19.5px; line-height: 24px; letter-spacing: 0.01em;
  }
  .person-role { font-weight: 500; font-size: 18px; line-height: 22px; letter-spacing: 0.02em; }
  .address { margin-top: 16px; font-size: 17.5px; line-height: 23px; }
  .contact-list { list-style: none; margin-top: 6px; }
  .contact-list li {
    display: flex; align-items: center; gap: 6px;
    font-size: 18px; line-height: 25px;
  }
  .contact-list svg { width: 19px; height: 19px; flex: none; }

  .back-photo {
    position: absolute; left: 78px; top: 0; width: 510px; height: 100%;
    background: radial-gradient(ellipse at 55% 40%, var(--navy-soft) 0%, rgba(24,27,39,0) 70%);
  }
  .back-brand {
    position: absolute; inset: 0;
    display: flex; align-items: center; justify-content: center;
  }
  .back-brand .brand-name { font-size: 56px; color: var(--on-dark); }
</style>
</head>
<body>
<div class="sheet">
  <section class="card card--front">
    <div class="front-brand">
      <span class="brand-name">Veltmoor</span>
    </div>
    <div class="front-details">
      <p class="person-name">MARA DELVEN</p>
      <p class="person-role">Managing Director</p>
      <p class="address">48 Linden Crest Road,<br>Oakvale, ON K2M 4R7</p>
      <ul class="contact-list">
        <li>
          <svg viewBox="0 0 24 24" aria-hidden="true"><path fill="#fff" d="M6.6 10.8a15.2 15.2 0 0 0 6.6 6.6l2.2-2.2a1 1 0 0 1 1-.25 11.4 11.4 0 0 0 3.6.57 1 1 0 0 1 1 1V20a1 1 0 0 1-1 1A17 17 0 0 1 3 4a1 1 0 0 1 1-1h3.5a1 1 0 0 1 1 1c0 1.25.2 2.45.57 3.57a1 1 0 0 1-.25 1z"/></svg>
          +15550192846
        </li>
        <li>
          <svg viewBox="0 0 24 24" aria-hidden="true"><rect x="2" y="5" width="20" height="14" fill="#fff"/><path d="M2.5 5.5 12 13l9.5-7.5M2.5 18.5l7-6.5M21.5 18.5l-7-6.5" stroke="var(--ink)" stroke-width="1.4" fill="none"/></svg>
          hello@veltmoor.com
        </li>
        <li>
          <svg viewBox="0 0 24 24" aria-hidden="true"><g fill="none" stroke="#fff" stroke-width="1.6"><circle cx="12" cy="12" r="9.5"/><ellipse cx="12" cy="12" rx="4.2" ry="9.5"/><path d="M2.5 12h19M4 7h16M4 17h16"/></g></svg>
          www.veltmoor.com
        </li>
      </ul>
    </div>
  </section>

  <section class="card card--back">
    <div class="back-photo" role="img" aria-label="Faint photograph of a leaping dancer holding flowing fabric"></div>
    <div class="back-brand">
      <span class="brand-name">Veltmoor</span>
    </div>
  </section>
</div>
</body>
</html>
```